Awesome design needed for standup comedy portal

We need a website designed for a new portal (grinbox.net) dedicated to standup comedy.

- homepage
- featured "hero" content at top
- banner advertising
- browse comics
- browse venues
- search
- signup / login
- social media links

- comic page
- name
- pictures
- calendar of performances
- list of albums (with buy buttons)
- list of specials (Vexora, Plumtrack, etc. with buy buttons)
- reviews
- latest tweets
- latests pixaloop photos
- links to social media accounts
- links to filmdex, podcast

- venue page
- name
- pictures
- address, phone number
- calendar of events
- reviews
- latest tweets
- links to filmdex, podcast

Target Market(s)

Fans of standup comedy and comedians

Number of Pages Required

Font styles to use
Sans Serif

Requirements
Must have
• Will eventually be implemented in bootstrap, so please keep that in mind

```html
<!DOCTYPE html>
<html lang="en">
<head>
<meta charset="utf-8">
<title>Grinbox – Standup Comedy</title>
<link href="https://fonts.googleapis.com/css2?family=Exo+2:wght@500;600;700;800&family=Open+Sans:wght@400;600;700&display=swap" rel="stylesheet">
<style>
:root{
  --red:#c4161c;
  --red-dark:#6e1410;
  --curtain:#8a2113;
  --curtain-deep:#5e150c;
  --ink:#111214;
  --night:#1a1d22;
  --brown:#4a3324;
  --brown-dark:#33231a;
  --panel:#4a1b14;
  --white:#ffffff;
  --muted:#d9d2cc;
  --grey:#5c5c5c;
  --gold:#e2a14a;
}
*{box-sizing:border-box;margin:0;padding:0}
html,body{width:1200px;height:2675px;overflow:hidden}
body{position:relative;background:var(--ink);font-family:"Open Sans",sans-serif;color:var(--white)}
.abs{position:absolute}
.heading{font-family:"Exo 2",sans-serif;font-weight:700;text-transform:uppercase;letter-spacing:1px}

/* hero */
.hero{left:0;top:0;width:1200px;height:654px;background:radial-gradient(ellipse at 55% 40%,#3b4a55 0%,#1f2a31 45%,#0e1215 100%)}
.hero-photo{left:380px;top:0;width:820px;height:567px;background:radial-gradient(ellipse at 45% 45%,#5a6b74 0%,#2a353c 55%,rgba(20,25,29,0) 80%)}
.brand{left:100px;top:58px;display:flex;align-items:center;gap:10px}
.brand-dot{width:44px;height:44px;border-radius:50%;background:var(--red)}
.brand-name{font-family:"Exo 2",sans-serif;font-weight:800;font-size:34px;color:var(--white)}
.top-search{left:713px;top:37px;width:214px;height:28px;border-radius:14px;background:var(--white);color:#888;font-size:10px;padding:7px 14px}
.top-search svg{position:absolute;right:12px;top:8px}
.btn-login{left:947px;top:37px;width:70px;height:28px;border:1px solid #9aa;border-radius:3px;font-size:11px;text-align:center;line-height:26px}
.btn-signup{left:1030px;top:37px;width:72px;height:28px;background:var(--red);border-radius:3px;font-size:11px;text-align:center;line-height:28px}
.nav{left:525px;top:92px;display:flex;font-family:"Exo 2",sans-serif;font-weight:700;font-size:13px;text-transform:uppercase}
.nav a{color:var(--white);text-decoration:none;padding:6px 20px}
.nav a.active{border:1px solid var(--white);border-radius:15px}
.hero-title{left:98px;top:306px;font-family:"Exo 2",sans-serif;font-weight:800;line-height:1.05}
.hero-title .t1{font-size:48px}
.hero-title .t2{font-size:40px}
.arrow{width:36px;height:36px;border-radius:50%;background:#000;top:342px}
.search-band{left:0;top:567px;width:1200px;height:87px;background:rgba(10,12,14,.7)}
.comic-search{left:280px;top:590px;width:472px;height:42px;background:var(--white);color:#888;font-size:13px;padding:12px 16px}
.comic-search svg{position:absolute;right:16px;top:14px}
.btn-search{left:767px;top:590px;width:155px;height:42px;background:var(--red);font-family:"Exo 2",sans-serif;font-weight:700;font-size:15px;text-align:center;line-height:42px}

/* welcome */
.welcome{left:0;top:654px;width:1200px;height:337px;background:radial-gradient(ellipse at 50% 45%,var(--curtain) 0%,#741a0f 55%,var(--curtain-deep) 100%)}
.mic{left:1010px;top:44px;width:110px;height:293px;background:linear-gradient(180deg,#b89890,#6e4a44)}
.welcome h2{position:absolute;left:0;width:1200px;top:86px;text-align:center;font-size:34px}
.welcome p{position:absolute;left:155px;width:890px;text-align:center;font-size:11px;line-height:17px;color:var(--muted)}

/* venues */
.venues{left:0;top:991px;width:1200px;height:537px;background:linear-gradient(180deg,#26262a 0%,#121214 100%)}
.venues h2{position:absolute;left:0;width:1200px;top:48px;text-align:center;font-size:34px}
.venue-card{top:125px;width:324px;height:337px}
.venue-photo{width:324px;height:196px;background:linear-gradient(135deg,#2a3a4e,#1a1422 60%,#4a2a55)}
.venue-body{height:141px;background:var(--panel);text-align:center;padding:14px 18px}
.venue-body h3{font-family:"Open Sans",sans-serif;font-weight:600;font-size:14px;text-transform:uppercase;margin-bottom:8px}
.venue-body p{font-size:11px;line-height:16px;color:var(--muted)}
.venue-body .book{display:block;margin-top:10px;font-size:11px;color:var(--gold);text-transform:uppercase}

/* events */
.events{left:0;top:1528px;width:1200px;height:777px;background:linear-gradient(180deg,var(--brown) 0%,var(--brown-dark) 100%)}
.events h2{position:absolute;left:0;width:1200px;top:66px;text-align:center;font-size:34px}
.event-card{top:146px;width:488px;height:179px;background:var(--white);color:var(--grey)}
.event-photo{left:3px;top:3px;width:182px;height:173px;background:linear-gradient(160deg,#8a6a60,#3a2a2a)}
.event-body{left:210px;top:14px;width:262px}
.event-body h3{font-family:"Open Sans",sans-serif;font-weight:400;font-size:16px;color:#444;margin-bottom:10px}
.date{display:inline-block;background:var(--red);color:var(--white);font-size:11px;font-weight:600;padding:3px 7px}
.comments{font-size:10px;font-style:italic;margin-left:12px}
.event-body p{margin-top:10px;font-size:11px;line-height:17px}
.banner{left:100px;top:374px;width:1000px;height:334px;background:linear-gradient(180deg,#e1475a 0%,#5a2a6a 35%,#4a2060 100%)}
.banner-text{left:170px;top:170px;text-align:center}
.banner-text .b1{font-family:"Exo 2",sans-serif;font-weight:800;font-size:30px}
.banner-text .b2{font-family:"Exo 2",sans-serif;font-weight:700;font-size:22px;margin-top:18px}
.banner-text .b3{font-family:"Exo 2",sans-serif;font-weight:700;font-size:34px}

/* footer */
.footer{left:0;top:2305px;width:1200px;height:307px;background:var(--night)}
.footer h4{font-family:"Exo 2",sans-serif;font-weight:600;font-size:18px;text-transform:uppercase;position:absolute}
.field{border:1px solid #cfcfcf;font-size:10px;color:#ddd;padding:5px 8px}
.btn-submit{border:1px solid #cfcfcf;border-radius:3px;font-size:14px;font-weight:600;text-align:center;line-height:32px}
.contact-lines{left:683px;top:2400px;font-size:12px;line-height:19px}
.contact-row{display:flex;align-items:center;gap:14px;margin-top:12px;font-size:12px}
.quick{left:990px;top:2393px;list-style:none;font-size:12px;line-height:23px}
.quick li::before{content:"";display:inline-block;width:0;height:0;border-left:5px solid var(--white);border-top:4px solid transparent;border-bottom:4px solid transparent;margin-right:12px}
.bottom-bar{left:0;top:2612px;width:1200px;height:63px;background:#232427;text-align:center;font-size:12px;line-height:63px;color:#cfcfcf}
</style>
</head>
<body>

<section class="abs hero">
  <div class="abs hero-photo" role="img" aria-label="Ventriloquist performing on stage with a red-haired puppet"></div>
  <div class="abs brand"><span class="brand-dot"></span><span class="brand-name">Grinbox</span></div>
  <div class="abs top-search">Search
    <svg width="11" height="11" viewBox="0 0 11 11"><circle cx="4.5" cy="4.5" r="3.5" fill="none" stroke="#777" stroke-width="1.4"/><line x1="7" y1="7" x2="10" y2="10" stroke="#777" stroke-width="1.4"/></svg>
  </div>
  <div class="abs btn-login">LOG IN</div>
  <div class="abs btn-signup">SIGN UP</div>
  <nav class="abs nav">
    <a class="active">Home</a><a>About</a><a>Services</a><a>Comics</a><a>Venues</a><a>Contact Us</a>
  </nav>
  <div class="abs hero-title">
    <div class="t1">GRINBOX</div>
    <div class="t2">STANDUP COMEDY</div>
  </div>
  <svg class="abs arrow" style="left:32px" viewBox="0 0 36 36"><polyline points="21,11 14,18 21,25" fill="none" stroke="#fff" stroke-width="2.5"/></svg>
  <svg class="abs arrow" style="left:1128px" viewBox="0 0 36 36"><polyline points="15,11 22,18 15,25" fill="none" stroke="#fff" stroke-width="2.5"/></svg>
  <div class="abs search-band"></div>
  <div class="abs comic-search">Search comics
    <svg width="13" height="13" viewBox="0 0 11 11"><circle cx="4.5" cy="4.5" r="3.5" fill="none" stroke="#777" stroke-width="1.2"/><line x1="7" y1="7" x2="10" y2="10" stroke="#777" stroke-width="1.2"/></svg>
  </div>
  <div class="abs btn-search">SEARCH NOW</div>
</section>

<section class="abs welcome" role="img" aria-label="Red stage curtain backdrop">
  <div class="abs mic" role="img" aria-label="Vintage stage microphone"></div>
  <h2 class="heading">Welcome to Grinbox</h2>
  <p style="top:142px">Sed ut perspiciatis unde omnis iste natus error sit voluptatem accusantium doloremque laudantium, totam rem aperiam, eaque ipsa quae ab illo inventore veritatis et quasi architecto beatae vitae dicta sunt explicabo. Nemo enim ipsam voluptatem quia voluptas sit aspernatur aut odit aut fugit, sed quia consequuntur magni dolores eos qui ratione voluptatem sequi nesciunt. Neque porro quisquam est, qui dolorem</p>
  <p style="top:214px">Sed ut perspiciatis unde omnis iste natus error sit voluptatem accusantium doloremque laudantium, totam rem aperiam, eaque ipsa quae ab illo inventore veritatis et quasi architecto beatae vitae dicta sunt explicabo. Nemo enim ipsam voluptatem quia voluptas</p>
</section>

<section class="abs venues">
  <h2 class="heading">Venues</h2>
  <article class="abs venue-card" style="left:100px">
    <div class="venue-photo" role="img" aria-label="Ventriloquist with puppet on stage"></div>
    <div class="venue-body"><h3>Sed ut perspiciatis unde</h3><p>Lorem ipsum dolor sit amet, consectetur adipiscing elit, sed do eiusmod tempor incididunt ut labore et dolore magna aliqua.</p><span class="book">Book the table ⊕</span></div>
  </article>
  <article class="abs venue-card" style="left:437px">
    <div class="venue-photo" role="img" aria-label="Comedian with microphone on a starry stage"></div>
    <div class="venue-body"><h3>Sed ut perspiciatis unde</h3><p>Lorem ipsum dolor sit amet, consectetur adipiscing elit, sed do eiusmod tempor incididunt ut labore et dolore magna aliqua.</p><span class="book">Book the table ⊕</span></div>
  </article>
  <article class="abs venue-card" style="left:776px">
    <div class="venue-photo" role="img" aria-label="Performer with puppet under purple stage lights"></div>
    <div class="venue-body"><h3>Sed ut perspiciatis unde</h3><p>Lorem ipsum dolor sit amet, consectetur adipiscing elit, sed do eiusmod tempor incididunt ut labore et dolore magna aliqua.</p><span class="book">Book the table ⊕</span></div>
  </article>
</section>

<section class="abs events">
  <h2 class="heading">Upcoming Events</h2>
  <article class="abs event-card" style="left:100px">
    <div class="abs event-photo" role="img" aria-label="Audience laughing in a theatre"></div>
    <div class="abs event-body">
      <h3>Nulla at diam ornare, aliquam</h3>
      <span class="date">MAY 25, 2017</span><span class="comments">2 comments</span>
      <p>Nulla at diam ornare, aliquam urna vel, commodo urna. Nam id risus a est luctus consectetur quis eget libero. Suspendisse potenti. Pellentesque habitant morbi tristique senectus</p>
    </div>
  </article>
  <article class="abs event-card" style="left:613px">
    <div class="abs event-photo" role="img" aria-label="Costumed stage performers"></div>
    <div class="abs event-body">
      <h3>Nulla at diam ornare, aliquam</h3>
      <span class="date">MAY 25, 2017</span><span class="comments">2 comments</span>
      <p>Nulla at diam ornare, aliquam urna vel, commodo urna. Nam id risus a est luctus consectetur quis eget libero. Suspendisse potenti. Pellentesque habitant morbi tristique senectus</p>
    </div>
  </article>
  <div class="abs banner" role="img" aria-label="Advertising banner: theatre curtains with comedy masks and stage props">
    <div class="abs banner-text">
      <div class="b1">Grinbox</div>
      <div class="b2">STANDUP</div>
      <div class="b3">COMEDY</div>
    </div>
  </div>
</section>

<footer class="abs footer">
  <div class="abs brand" style="top:96px"><span class="brand-dot"></span><span class="brand-name">Grinbox</span></div>
  <h4 style="left:325px;top:52px">Get Quote</h4>
  <div class="abs field" style="left:325px;top:93px;width:146px;height:38px;line-height:26px">Name</div>
  <div class="abs field" style="left:480px;top:93px;width:146px;height:38px;line-height:26px">Phone</div>
  <div class="abs field" style="left:325px;top:138px;width:301px;height:68px">Message</div>
  <div class="abs btn-submit" style="left:325px;top:222px;width:107px;height:34px">SUBMIT</div>
  <h4 style="left:683px;top:56px">Contact Us</h4>
  <h4 style="left:990px;top:48px">Quick Links</h4>
</footer>
<div class="abs contact-lines">
  <div>Grinbox</div>
  <div>12 Larkfield Lane, 90417</div>
  <div>&nbsp;Brightvale, California.</div>
  <div class="contact-row"><svg width="16" height="16" viewBox="0 0 16 16"><path d="M3 1l3 3-2 2c1 2 3 4 5 5l2-2 3 3-2 3C7 14 2 9 1 3z" fill="none" stroke="#fff" stroke-width="1.2"/></svg>Phone: +610 555 0142</div>
  <div class="contact-row"><svg width="16" height="12" viewBox="0 0 16 12"><rect x="1" y="1" width="14" height="10" fill="none" stroke="#fff" stroke-width="1.2"/><polyline points="1,1 8,7 15,1" fill="none" stroke="#fff" stroke-width="1.2"/></svg>info@grinbox.net</div>
</div>
<ul class="abs quick">
  <li>Home</li><li>About Us</li><li>Venues</li><li>Testimonials</li><li>Contact</li><li>Get Quote</li>
</ul>
<div class="abs bottom-bar">Copyright 2017 | All Rights Reserved – Grinbox</div>

</body>
</html>
```